The Wagon Pulls Over is a food truck, talent show, fundraiser event.

The Belmere Uplift Foundation is hosting a food truck, talent show, fundraiser called The Wagon Pulls Over. We need a flyer designed that incorporates a couple of our existing logos. The theme this year is "Summer Break Jam." The event will be held Wednesday, May 23rd from 3-6 pm at the BRAND NEW Lakeside Meridian Amphitheater (R). I've included some of our logos to incorporate into the flyer. This event is geared towards kids K-12.

Target Market(s)

Kids (K-12) and parents

Industry/Entity Type

Non Profit

Colors

Designer to choose colors to be used in the design.

Requirements
Must have
• Incorporate both logos: Truck (prominent), Foundation logo (not as prominent).
Nice to have
• Might need to have some space to add sponsor logos. Not a must.

```html
<!DOCTYPE html>
<html lang="en">
<head>
<meta charset="utf-8">
<title>Summer Break Jam Flyer</title>
<link rel="stylesheet" href="https://fonts.googleapis.com/css2?family=Oswald:wght@400;500;600&family=Montserrat:wght@300;400;600;700&display=swap">
<style>
  :root {
    --page-bg: #e4e4e4;
    --navy: #173f7f;
    --navy-light: #2a5aa3;
    --navy-dark: #0f2f63;
    --gold: #d9a818;
    --gold-light: #f0c63a;
    --gold-dark: #b18608;
    --white: #ffffff;
    --silver: #e9e9ea;
    --silver-dark: #c9cacc;
    --photo-warm: #b88a6e;
    --photo-cool: #8fa0b3;
  }
  * { margin: 0; padding: 0; box-sizing: border-box; }
  html, body { width: 707px; height: 1200px; overflow: hidden; }
  body { background: var(--page-bg); position: relative; }

  .flyer {
    position: absolute; left: 0; top: 100px;
    width: 707px; height: 1000px; overflow: hidden;
    background: radial-gradient(ellipse at 55% 60%, var(--navy-light) 0%, var(--navy) 55%, var(--navy-dark) 100%);
    font-family: "Montserrat", sans-serif; color: var(--white);
  }
  .flyer-art { position: absolute; inset: 0; }

  .truck-badge {
    position: absolute; left: 421px; top: 28px; width: 244px; height: 244px;
    border-radius: 50%;
    display: flex; align-items: center; justify-content: center; text-align: center;
    font-family: "Oswald", sans-serif; font-weight: 600; font-size: 30px; line-height: 1.1;
    color: var(--navy); text-transform: uppercase; letter-spacing: 1px;
  }

  .foundation-name {
    position: absolute; left: 500px; top: 420px; width: 176px; text-align: center;
    font-family: "Montserrat", sans-serif; font-weight: 700; color: var(--white);
    text-transform: uppercase; line-height: 1.15;
  }
  .foundation-name span { display: block; }
  .foundation-name .line-a { font-size: 20px; }
  .foundation-name .line-b { font-size: 17px; }
  .foundation-name .line-c { font-size: 11px; letter-spacing: 2px; }

  .event-title {
    position: absolute; left: 87px; top: 630px; width: 536px; height: 50px;
    display: flex; align-items: center; justify-content: center;
    font-family: "Oswald", sans-serif; font-weight: 500; font-size: 40px;
    color: var(--white); text-transform: uppercase; letter-spacing: 0.5px;
    text-shadow: 0 2px 3px rgba(0,0,0,0.25);
  }

  .details-box {
    position: absolute; left: 122px; top: 730px; width: 461px; height: 120px;
    border: 1.5px solid rgba(255,255,255,0.85);
    text-align: center; padding-top: 24px;
  }
  .details-box .box-label {
    position: absolute; left: 50%; top: -27px; transform: translateX(-50%);
    padding: 0 12px; background: var(--navy);
    font-family: "Oswald", sans-serif; font-weight: 500; font-size: 34px; line-height: 1.3;
  }
  .details-line {
    font-size: 25px; font-weight: 400; line-height: 1.25; text-transform: uppercase;
  }
  .details-line b { font-weight: 700; }
  .details-line sup { font-size: 13px; vertical-align: 11px; }
  .venue-line {
    font-family: "Oswald", sans-serif; font-weight: 500; font-size: 22px; line-height: 1.4;
  }

  .audience-note {
    position: absolute; left: 0; top: 857px; width: 707px; text-align: center;
    font-weight: 300; font-size: 22px; text-transform: uppercase;
  }

  .sponsor-band {
    position: absolute; left: 0; top: 918px; width: 707px; height: 82px;
    background: linear-gradient(180deg, var(--white) 0%, var(--silver) 60%, var(--silver-dark) 100%);
  }
  .sponsor-tag {
    position: absolute; left: 263px; top: 906px; width: 185px; height: 26px;
    background: linear-gradient(180deg, var(--gold-light), var(--gold));
    color: var(--navy-dark); font-size: 11px; font-weight: 600;
    display: flex; align-items: center; justify-content: center;
  }
  .web-tab {
    position: absolute; left: 232px; top: 972px; width: 243px; height: 28px;
    display: flex; align-items: center; justify-content: center; gap: 6px;
    font-size: 11px; font-weight: 600; color: var(--white);
  }
  .web-tab .dot { width: 10px; height: 10px; border: 1.5px solid var(--white); border-radius: 50%; }
</style>
</head>
<body>
<main class="flyer">
  <svg class="flyer-art" width="707" height="1000" viewBox="0 0 707 1000" aria-hidden="false">
    <defs>
      <linearGradient id="photo-tone" x1="0" y1="0" x2="1" y2="1">
        <stop offset="0" stop-color="#d9d2c8"/>
        <stop offset="0.45" stop-color="var(--photo-cool)"/>
        <stop offset="1" stop-color="var(--photo-warm)"/>
      </linearGradient>
      <radialGradient id="badge-face" cx="0.45" cy="0.4" r="0.7">
        <stop offset="0" stop-color="#ffffff"/>
        <stop offset="1" stop-color="#cfd2d6"/>
      </radialGradient>
      <linearGradient id="ribbon-gold" x1="0" y1="0" x2="0" y2="1">
        <stop offset="0" stop-color="var(--gold-light)"/>
        <stop offset="1" stop-color="var(--gold-dark)"/>
      </linearGradient>
    </defs>

    <!-- photo circle -->
    <circle cx="150" cy="246" r="378" fill="none" stroke="rgba(255,255,255,0.6)" stroke-width="1.2"/>
    <circle class="photo-area" cx="142" cy="235" r="367" fill="url(#photo-tone)" role="img" aria-label="Photo of smiling students with backpacks running down a school walkway"/>

    <!-- truck badge disc -->
    <circle cx="543" cy="150" r="124" fill="url(#badge-face)" stroke="#b9bec6" stroke-width="3"/>

    <!-- ribbon -->
    <polygon points="87,628 623,628 606,654 623,680 87,680 104,654" fill="url(#ribbon-gold)"/>

    <!-- website tab -->
    <polygon points="232,1000 245,972 462,972 475,1000" fill="var(--navy)"/>
  </svg>

  <div class="truck-badge">The Wagon<br>Pulls Over</div>

  <div class="foundation-name">
    <span class="line-a">Belmere</span>
    <span class="line-b">Uplift</span>
    <span class="line-c">Foundation</span>
  </div>

  <h1 class="event-title">Summer Break Jam</h1>

  <section class="details-box">
    <h2 class="box-label">EVENT</h2>
    <p class="details-line"><b>Date-</b>Wednesday, May 23<sup>RD</sup></p>
    <p class="details-line"><b>Time-</b>3-6 PM</p>
    <p class="venue-line">BRAND NEW Lakeside Meridian Amphitheater®</p>
  </section>

  <p class="audience-note">This event is geared towards kids K-12.</p>

  <div class="sponsor-band"></div>
  <div class="sponsor-tag">Add Sponsor Logos Here</div>
  <div class="web-tab"><span class="dot"></span>www.belmereuplift.org</div>
</main>
</body>
</html>
```